Packaging Design for Vanta Prime

We require an outstanding packaging design for our Vanta Prime brand, which offers hydration electrolyte supplements specifically tailored for athletes and sporty individuals.

Benchmark packaging design from quellix competitor attached. The product packaging contains 20 x 20g sticks of the product.

Target Market

Psychographic: Health-conscious, active lifestyle, values quality, functionality and sustainability.

product description 1:
HYDRATION BOOSTER
Refresh, Replenish, Recharge!

product description 2:
PREMIUM ISOTONIC ELECTROLYTE DRINK
Nutritional Expertise Since 1992.

Existing Logo: to add "since 1992"

Appeal to Target Market: Create a design that resonates with both men and women in the 25-55 age group.

Grafik Design: Develop a visually striking design that grabs attention in online retail environments like Brindleport.

Visuals: glass of water (or symbolic) and sticks (powder) just like benchmark brand quellix.

Design Elements
Use colours that are inside the Vanta-Prime Logo, attached.
Product will be available in 3 flavours. Lemon=yellow, Orange=orange, Black Currant=purple

Typography: Utilize strong, clean, and modern fonts. Ensure readability and create a sense of strength, endurance and reliability.

The product will be available in 3 flavours: Lemon, Orange and Johannisbeere

We look forward to seeing your creative ideas and innovative designs for our Vanta Prime brand packaging.

```html
<!DOCTYPE html>
<html lang="en">
<head>
<meta charset="utf-8">
<title>Vanta Prime Hydration Booster – Pouch Range</title>
<link rel="stylesheet" href="https://fonts.googleapis.com/css2?family=Poppins:wght@400;500;600;700;800&display=swap">
<style>
  :root{
    --stage:#dedede;
    --navy:#2444a2;
    --navy-deep:#1c3790;
    --brand-yellow:#e8f01c;
    --white:#ffffff;
    --badge:#e8f01c;
    --badge-ink:#1c3790;
  }
  *{box-sizing:border-box;margin:0;padding:0}
  html,body{width:1200px;height:720px;overflow:hidden}
  body{background:var(--stage);font-family:"Poppins",sans-serif;position:relative}

  .range{position:absolute;left:60px;top:0;width:1080px;height:720px;display:flex;gap:30px;align-items:center}

  .pouch{position:relative;width:330px;height:490px;font-size:9.2px;overflow:hidden;border-radius:3px 3px 10px 10px;color:var(--white)}
  .pouch--lead{width:360px;height:530px;font-size:10px}

  .pouch--blackcurrant{--flav-top:#3a0a5c;--flav-bottom:#c42a9c;--band:#e2148c;--accent:#e2148c;--pill:#e2148c;--pill-ink:#4a0a3e;--feature:#ead6f0;--strip:#4a1a6a}
  .pouch--lemon{--flav-top:#0a8a3a;--flav-bottom:#e6ee22;--band:#f2f01c;--accent:#f2f01c;--pill:#e8ea1c;--pill-ink:#0a6a2a;--feature:#0c5a24;--strip:#1c8a3a}
  .pouch--orange{--flav-top:#ff4820;--flav-bottom:#ffb41e;--band:#ffc21c;--accent:#ffd21c;--pill:#ffcc1c;--pill-ink:#e43e10;--feature:#e43010;--strip:#ff4a22}

  .pouch__bg{position:absolute;inset:0;width:100%;height:100%}

  .seal{position:absolute;left:0;right:0;top:7%;border-top:1px dashed #0d1a40;opacity:.7}

  .count{position:absolute;left:6%;top:0;width:2.9em;background:var(--badge);color:var(--badge-ink);text-align:center;padding:.5em 0 .35em;line-height:1}
  .count__num{display:block;font-size:2.6em;font-weight:800;letter-spacing:-.04em}
  .count__unit{display:block;font-size:.82em;font-weight:700;margin-top:.25em;color:#1a2a60}
  .net{position:absolute;left:6%;top:15.5%;font-size:.8em;font-weight:500;letter-spacing:.02em}

  .brand{position:absolute;left:27%;top:12%;transform:rotate(-10deg);transform-origin:left top;display:flex;align-items:center;gap:.5em}
  .brand__dot{width:2.4em;height:2.4em;border-radius:50%;background:var(--white)}
  .brand__name{font-size:3.4em;font-weight:800;color:var(--brand-yellow);line-height:1;letter-spacing:-.02em}
  .brand__since{position:absolute;right:0;top:100%;font-size:1em;font-weight:500;margin-top:.2em}

  .visual{position:absolute;right:3%;top:36%;width:40%;height:58%;border-radius:4px;
    background:
      linear-gradient(90deg,transparent 45%,rgba(255,255,255,.55) 55%,transparent 65%) top/100% 45% no-repeat,
      linear-gradient(180deg,rgba(255,255,255,.08) 45%,rgba(255,255,255,.35) 60%,rgba(255,255,255,.55) 100%)}

  .copy{position:absolute;left:7%;top:42%;width:62%}
  .headline{font-size:3.6em;font-weight:700;line-height:1.02;letter-spacing:-.01em}
  .tagline{margin-top:.7em;font-size:1.15em;font-weight:600;color:var(--accent);white-space:nowrap}
  .product-type{margin-top:1.9em;font-size:1.9em;font-weight:700;line-height:1.2;white-space:nowrap}
  .features{margin-top:.9em;display:flex;flex-wrap:wrap;gap:.4em 1.1em;font-size:1.1em;font-weight:500;color:var(--feature);list-style:none;width:140%}
  .features li{display:flex;align-items:center;gap:.35em}
  .features svg{width:1.1em;height:1.1em;fill:currentColor}

  .flavour{position:absolute;left:50%;bottom:10.5%;transform:translateX(-50%);background:var(--pill);color:var(--pill-ink);font-weight:700;font-size:1.2em;letter-spacing:.06em;padding:.3em 2.6em;border-radius:2em}
  .footer{position:absolute;left:0;right:0;bottom:3.5%;text-align:center;font-size:.95em;font-weight:500;letter-spacing:.22em}
</style>
</head>
<body>
<main class="range">

  <article class="pouch pouch--blackcurrant">
    <svg class="pouch__bg" viewBox="0 0 100 150" preserveAspectRatio="none" aria-hidden="true">
      <defs><linearGradient id="g-bc" x1="0" y1="0" x2="0" y2="1"><stop offset="0" stop-color="#3a0a5c"/><stop offset="1" stop-color="#c42a9c"/></linearGradient></defs>
      <rect width="100" height="150" fill="url(#g-bc)"/>
      <rect y="139" width="100" height="11" fill="#4a1a6a"/>
      <path d="M0 0H100V48Q50 74 0 46Z" fill="#e2148c"/>
      <path d="M0 0H100V44Q50 69 0 42Z" fill="#2444a2"/>
    </svg>
    <div class="seal"></div>
    <div class="count"><span class="count__num">16</span><span class="count__unit">STICKS</span></div>
    <p class="net">NET WT 9oz /256g</p>
    <div class="brand"><span class="brand__dot"></span><span class="brand__name">Vanta Prime</span><span class="brand__since">Since 1992</span></div>
    <div class="visual" role="img" aria-label="Glass of blackcurrant drink with electrolyte powder pouring in"></div>
    <div class="copy">
      <h2 class="headline">HYDRATION<br>BOOSTER</h2>
      <p class="tagline">REFRESH, REPLENISH &amp; RECHARGE!</p>
      <p class="product-type">PREMIUM ISOTONIC<br>ELECTROLYTE DRINK</p>
      <ul class="features">
        <li><svg viewBox="0 0 10 10"><path d="M6 0L2 6h3l-1 4 4-6H5z"/></svg>Fast Rehydration</li>
        <li><svg viewBox="0 0 10 10"><path d="M5 10V5C5 2 7 1 9 1 9 4 7 5 5 5 3 5 1 4 1 1 3 1 5 2 5 5z"/></svg>Natural Flavors</li>
        <li><svg viewBox="0 0 10 10"><path d="M4 1h2v3h3v2H6v3H4V6H1V4h3z"/></svg>Vitamins &amp; Minerals</li>
      </ul>
    </div>
    <p class="flavour">BLACKCURRANT</p>
    <p class="footer">NUTRITIONAL EXPERTISE SINCE 1992</p>
  </article>

  <article class="pouch pouch--lemon pouch--lead">
    <svg class="pouch__bg" viewBox="0 0 100 150" preserveAspectRatio="none" aria-hidden="true">
      <defs><linearGradient id="g-lm" x1="0" y1="0" x2="0" y2="1"><stop offset=".3" stop-color="#0a8a3a"/><stop offset=".62" stop-color="#1cc44a"/><stop offset="1" stop-color="#e6ee22"/></linearGradient></defs>
      <rect width="100" height="150" fill="url(#g-lm)"/>
      <rect y="139" width="100" height="11" fill="#1c8a3a"/>
      <path d="M0 0H100V46Q50 72 0 44Z" fill="#f2f01c"/>
      <path d="M0 0H100V42Q50 67 0 40Z" fill="#2444a2"/>
    </svg>
    <div class="seal"></div>
    <div class="count"><span class="count__num">16</span><span class="count__unit">STICKS</span></div>
    <p class="net">NET WT 9oz /256g</p>
    <div class="brand"><span class="brand__dot"></span><span class="brand__name">Vanta Prime</span><span class="brand__since">Since 1992</span></div>
    <div class="visual" role="img" aria-label="Glass of lemon drink with electrolyte powder pouring in"></div>
    <div class="copy">
      <h2 class="headline">HYDRATION<br>BOOSTER</h2>
      <p class="tagline">REFRESH, REPLENISH &amp; RECHARGE!</p>
      <p class="product-type">PREMIUM ISOTONIC<br>ELECTROLYTE DRINK</p>
      <ul class="features">
        <li><svg viewBox="0 0 10 10"><path d="M6 0L2 6h3l-1 4 4-6H5z"/></svg>Fast Rehydration</li>
        <li><svg viewBox="0 0 10 10"><path d="M5 10V5C5 2 7 1 9 1 9 4 7 5 5 5 3 5 1 4 1 1 3 1 5 2 5 5z"/></svg>Natural Flavors</li>
        <li><svg viewBox="0 0 10 10"><path d="M4 1h2v3h3v2H6v3H4V6H1V4h3z"/></svg>Vitamins &amp; Minerals</li>
      </ul>
    </div>
    <p class="flavour">LEMON</p>
    <p class="footer">NUTRITIONAL EXPERTISE SINCE 1992</p>
  </article>

  <article class="pouch pouch--orange">
    <svg class="pouch__bg" viewBox="0 0 100 150" preserveAspectRatio="none" aria-hidden="true">
      <defs><linearGradient id="g-or" x1="0" y1="0" x2="0" y2="1"><stop offset=".3" stop-color="#ff4820"/><stop offset="1" stop-color="#ffb41e"/></linearGradient></defs>
      <rect width="100" height="150" fill="url(#g-or)"/>
      <rect y="139" width="100" height="11" fill="#ff4a22"/>
      <path d="M0 0H100V48Q50 74 0 46Z" fill="#ffc21c"/>
      <path d="M0 0H100V44Q50 69 0 42Z" fill="#2444a2"/>
    </svg>
    <div class="seal"></div>
    <div class="count"><span class="count__num">16</span><span class="count__unit">STICKS</span></div>
    <p class="net">NET WT 9oz /256g</p>
    <div class="brand"><span class="brand__dot"></span><span class="brand__name">Vanta Prime</span><span class="brand__since">Since 1992</span></div>
    <div class="visual" role="img" aria-label="Glass of orange drink with electrolyte powder pouring in"></div>
    <div class="copy">
      <h2 class="headline">HYDRATION<br>BOOSTER</h2>
      <p class="tagline">REFRESH, REPLENISH &amp; RECHARGE!</p>
      <p class="product-type">PREMIUM ISOTONIC<br>ELECTROLYTE DRINK</p>
      <ul class="features">
        <li><svg viewBox="0 0 10 10"><path d="M6 0L2 6h3l-1 4 4-6H5z"/></svg>Fast Rehydration</li>
        <li><svg viewBox="0 0 10 10"><path d="M5 10V5C5 2 7 1 9 1 9 4 7 5 5 5 3 5 1 4 1 1 3 1 5 2 5 5z"/></svg>Natural Flavors</li>
        <li><svg viewBox="0 0 10 10"><path d="M4 1h2v3h3v2H6v3H4V6H1V4h3z"/></svg>Vitamins &amp; Minerals</li>
      </ul>
    </div>
    <p class="flavour">ORANGE</p>
    <p class="footer">NUTRITIONAL EXPERTISE SINCE 1992</p>
  </article>

</main>
</body>
</html>
```